Detail Shop Business card design

i need a business card design for my new detailing company called 'Brisk's Polish Works'. i want an all black and white design . simple, direct and to the point. i want the designer to choose a fitting font to match the logothe front should have logo, address, phone and email and the back side should have a slogan and text indicating that we offer services on anything including cars, trucks, motorcycles and RVs. slogan will read "we take pride in your ride"
maybe also very small on the back side the IG icon with Brisks_Polish_Works

phone 208.417.6352
address 3847 E Larkin Ave
Spokane WA 99214
email: BrisksPolish@mailvexo.com

Target Market(s)

all ages , auto enthusiasts

Industry/Entity Type

Automotive

Contact Information for Business Card

the front should have logo, address, phone and email and the back side should have a slogan and text indicating that we offer services on anything including cars, trucks, motorcycles and RVs. slogan will read "we take pride in your ride"

phone 208.417.6352
address 3847 E Larkin Ave
Spokane WA 99214

Colors
000000
ffffff

Requirements
Must have
• bold font and very simple design with good spacing
Nice to have
• anything creative from the designer indicating we service any types of vehicles
Should not have
• any colors ,

```html
<!DOCTYPE html>
<html lang="en">
<head>
<meta charset="utf-8">
<title>Brisk's Polish Works – Business Card</title>
<link href="https://fonts.googleapis.com/css2?family=Oswald:wght@500;700&family=Roboto+Condensed:wght@400;700&display=swap" rel="stylesheet">
<style>
  :root {
    --ink: #000000;
    --paper: #ffffff;
    --backdrop: #e6e6e6;
    --shade: rgba(0,0,0,0.18);
  }
  * { box-sizing: border-box; margin: 0; padding: 0; }
  html, body { width: 1200px; height: 950px; overflow: hidden; background: var(--backdrop); }
  .canvas { position: relative; width: 1200px; height: 950px; }
  .card {
    position: absolute; left: 215px; width: 770px; height: 440px;
    background: var(--paper); overflow: hidden;
    box-shadow: 0 6px 18px var(--shade);
  }
  .card--front { top: 24px; }
  .card--back { top: 486px; }

  .front-swoosh { position: absolute; inset: 0; width: 100%; height: 100%; }

  .brand {
    position: absolute; left: 48px; top: 196px;
    display: flex; align-items: center; gap: 12px;
    font-family: "Oswald", sans-serif; font-weight: 700;
    font-size: 27px; letter-spacing: 1px; text-transform: uppercase; color: var(--ink);
    white-space: nowrap;
  }
  .brand__dot { width: 20px; height: 20px; border-radius: 50%; background: var(--ink); flex: none; }

  .contact {
    position: absolute; right: 40px; top: 52px; text-align: right;
    font-family: "Roboto Condensed", sans-serif; color: var(--paper);
    white-space: nowrap;
  }
  .contact__name { font-weight: 700; font-size: 24px; letter-spacing: 1px; text-transform: uppercase; }
  .contact__role { font-size: 17px; letter-spacing: 1px; text-transform: uppercase; margin-bottom: 22px; }
  .contact__line {
    display: flex; justify-content: flex-end; align-items: center; gap: 10px;
    font-size: 17px; line-height: 30px;
  }
  .contact__icon { width: 16px; height: 16px; flex: none; }
  .contact__address { font-size: 17px; line-height: 24px; margin-top: 20px; }

  .vehicle-art {
    position: absolute; left: 170px; top: 48px; width: 430px; height: 230px;
    background: linear-gradient(160deg, #2a2a2a 0%, #000000 55%, #444444 100%);
    border-radius: 6px;
  }
  .slogan {
    position: absolute; left: 0; right: 0; top: 304px; text-align: center;
    font-family: "Oswald", sans-serif; font-weight: 700; font-size: 30px;
    letter-spacing: 2px; text-transform: uppercase; color: var(--ink);
  }
  .slogan-rule {
    position: absolute; left: 170px; width: 430px; top: 356px; height: 2px; background: var(--ink);
  }
  .services {
    position: absolute; left: 0; right: 0; top: 368px; text-align: center;
    font-family: "Roboto Condensed", sans-serif; font-weight: 700; font-size: 19px; color: var(--ink);
  }
</style>
</head>
<body>
<div class="canvas">

  <section class="card card--front" aria-label="Card front">
    <svg class="front-swoosh" viewBox="0 0 770 440" aria-hidden="true">
      <path d="M380 0 C500 0 500 150 420 240 C350 320 290 390 260 440 L770 440 L770 0 Z" fill="var(--ink)"/>
      <path d="M406 0 C525 10 520 160 438 250 C370 328 318 388 290 440" fill="none" stroke="var(--paper)" stroke-width="6"/>
    </svg>

    <div class="brand">
      <span class="brand__dot"></span>
      <span class="brand__name">Brisk's Polish Works</span>
    </div>

    <div class="contact">
      <p class="contact__name">Dale Mercer</p>
      <p class="contact__role">CEO/Founder</p>
      <p class="contact__line">208.417.6352
        <svg class="contact__icon" viewBox="0 0 16 16"><path d="M4 1 L6 5 L4.5 6.5 C5.5 8.5 7.5 10.5 9.5 11.5 L11 10 L15 12 L13.5 15 C7 14.5 1.5 9 1 2.5 Z" fill="var(--paper)"/></svg>
      </p>
      <p class="contact__line">208.552.7190
        <svg class="contact__icon" viewBox="0 0 16 16"><rect x="4" y="1" width="8" height="14" rx="1.5" fill="none" stroke="var(--paper)" stroke-width="1.6"/><circle cx="8" cy="12.5" r="1" fill="var(--paper)"/></svg>
      </p>
      <p class="contact__line">BrisksPolish@mailvexo.com
        <svg class="contact__icon" viewBox="0 0 16 16"><rect x="1" y="3" width="14" height="10" fill="var(--paper)"/><path d="M1 3 L8 9 L15 3" fill="none" stroke="var(--ink)" stroke-width="1.4"/></svg>
      </p>
      <p class="contact__line">www.briskspolish.com
        <svg class="contact__icon" viewBox="0 0 16 16"><circle cx="8" cy="8" r="6.5" fill="none" stroke="var(--paper)" stroke-width="1.5"/><ellipse cx="8" cy="8" rx="2.8" ry="6.5" fill="none" stroke="var(--paper)" stroke-width="1.2"/><line x1="1.5" y1="8" x2="14.5" y2="8" stroke="var(--paper)" stroke-width="1.2"/></svg>
      </p>
      <p class="contact__address">3847 E Larkin Ave<br>Spokane WA 99214</p>
    </div>
  </section>

  <section class="card card--back" aria-label="Card back">
    <div class="vehicle-art" role="img" aria-label="Black and white illustration of a classic hot rod car in side view"></div>
    <p class="slogan">We Take Pride in Your Ride</p>
    <div class="slogan-rule"></div>
    <p class="services">Services on anything including cars, trucks, motorcycles &amp; RVs</p>
  </section>

</div>
</body>
</html>
```